Luxury Wine Label for New Startup Winery

We need a wine label for our new winery startup. We have worked with a local designer but do not feel the resulting label / logo have the elevation required to present our brand as a luxury wine. Our winery is called "Quailbrook Vineyards" and we are focused on extremely high quality hand crafted artisan and estate wines from the Pacific Northwest.
We would like to see designs that utilize a tree line, or other imagery that represents the "Quailbrook" part of our company name. Another interesting feature could be wood grain.
A logo will be required based on your design so please design with this in mind:
This logo should be consistent with the wine bottle label design, and should be representative of our high end exclusive wine while giving a sense of place (Oregon/ Pacific Northwest.)
I will supply an image of the design we received from our local designer, PLEASE NOTE: in general we do like wood grain and tree line concepts but feel the execution was poorly done.
ATTN: Logo design should be suitable for use on: Bottles (Red wine/rose/white wine), Bussiness cards, vehicle signage, business signage, etc
P.S.:
If you have a design that is not outside the box we are still interested in seeing it.
Label is for a burgundy style bottle with a label height of 3.5 - 4" and a width of 3.5-4"
any label <= 4"x4" and >=3.5"x3.5" will be acceptable:
HOWEVER Width should be greater than or equal to height due to the bottle format
Target Market(s)
Wine enthusiasts with adequate discretionary budgets to afford $100 bottles of wine.
Industry/Entity Type
Wine / Winery
Requirements
Must have
- A sense of luxury, a feel of exclusivity, and a theme consistent with our product and brand name
Nice to have
- Tree line, wood grain or other wood themes. Serif fonts
Should not have
- anything cheesy, off topic, hard to read script fonts or anything that makes the label hard to read from a few feet away or too busy

```html
<!DOCTYPE html>
<html lang="en">
<head>
<meta charset="utf-8">
<title>Quailbrook Vineyards – Syrah Label</title>
<link rel="stylesheet" href="https://fonts.googleapis.com/css2?family=Cinzel:wght@400;500&display=swap">
<style>
  :root {
    --page-bg: #8f8f8f;
    --label-dark: #1b1b1b;
    --label-light: #f6f6f4;
    --gold: #c8922a;
    --gold-light: #e9c56a;
    --gold-deep: #9a6a16;
    --ink-dark: #1f1f1f;
    --ink-light: #e4e4e4;
    --ink-soft: #b9b9b9;
    --ridge-dark: #4a4a4a;
    --ridge-light: #3a3a3a;
  }
  * { box-sizing: border-box; margin: 0; padding: 0; }
  html, body { width: 913px; height: 1200px; overflow: hidden; }
  body {
    background: var(--page-bg);
    font-family: "Cinzel", Georgia, serif;
    display: flex;
    flex-direction: column;
    align-items: center;
    justify-content: space-evenly;
  }
  .label {
    width: 560px;
    height: 488px;
    border-radius: 26px;
    display: flex;
    flex-direction: column;
    align-items: center;
    padding-top: 46px;
  }
  .label--dark { background: var(--label-dark); }
  .label--light { background: var(--label-light); }

  .brand-name {
    color: var(--gold);
    font-weight: 400;
    text-align: center;
    line-height: 1.05;
  }
  .brand-name__primary { display: block; font-size: 44px; letter-spacing: 4px; }
  .brand-name__secondary { display: block; font-size: 30px; letter-spacing: 6px; margin-top: 6px; }

  .landscape-art {
    margin-top: 30px;
    width: 390px;
    height: 150px;
    border-radius: 4px 4px 60% 60% / 4px 4px 30% 30%;
  }
  .label--dark .landscape-art {
    background: linear-gradient(180deg, var(--ridge-dark) 0%, var(--ridge-dark) 22%, var(--gold-deep) 48%, var(--gold-light) 78%, var(--gold) 100%);
  }
  .label--light .landscape-art {
    background: linear-gradient(180deg, #d8d8d8 0%, #cfcfcf 22%, var(--gold-deep) 48%, var(--gold-light) 78%, var(--gold) 100%);
  }

  .varietal {
    margin-top: 38px;
    color: var(--gold);
    font-size: 28px;
    letter-spacing: 5px;
  }
  .region {
    margin-top: 12px;
    font-size: 14px;
    letter-spacing: 7px;
  }
  .vintage {
    margin-top: 8px;
    font-size: 14px;
    letter-spacing: 7px;
  }
  .label--dark .region { color: var(--ink-soft); }
  .label--dark .vintage { color: var(--gold); }
  .label--light .region,
  .label--light .vintage { color: var(--ink-dark); font-size: 16px; }
</style>
</head>
<body>

  <section class="label label--dark">
    <h1 class="brand-name">
      <span class="brand-name__primary">Quailbrook</span>
      <span class="brand-name__secondary">Vineyards</span>
    </h1>
    <div class="landscape-art" role="img" aria-label="Line drawing of mountain peaks above a gold foil tree line on rolling hills"></div>
    <p class="varietal">Syrah</p>
    <p class="region">Williamette Valley</p>
    <p class="vintage">2024</p>
  </section>

  <section class="label label--light">
    <h2 class="brand-name">
      <span class="brand-name__primary">Quailbrook</span>
      <span class="brand-name__secondary">Vineyards</span>
    </h2>
    <div class="landscape-art" role="img" aria-label="Line drawing of mountain peaks above a gold foil tree line on rolling hills"></div>
    <p class="varietal">Syrah</p>
    <p class="region">Williamette Valley</p>
    <p class="vintage">2024</p>
  </section>

</body>
</html>
```